Product Designer Business Card

Small product design, engineering and prototyping firm in need of a clean, professional business card design. To support our 3D design and drawing services, we offer 3D printing, molding, and casting of plastics, silicones, resins, etc. Our logo can still be modified/changed if necessary. The red/orange color is preferred, but may be substituted with blue or green, potentially. Either way, the colour of the logo should be match/compliment colors used throughout the design. One thought is to have the logo/contact info on one side, with the other side describing services offered, like with a small icon of 3D printer, molding, casting, and computer with a 3D model on-screen.
Industry/Entity Type
Mechanical Engineering
Contact Information for Business Card
Company: Kelvar Design
Phone: 613-582-9047
Email: mark@kelvardesign.ca

```html
<!DOCTYPE html>
<html lang="en">
<head>
<meta charset="utf-8">
<title>Kelvar Design – Business Card</title>
<link rel="stylesheet" href="https://fonts.googleapis.com/css2?family=Poppins:wght@400;500&family=Roboto+Condensed:wght@500&display=swap">
<style>
  :root {
    --brand-red: #dc2000;
    --brand-red-light: #e84a2c;
    --deep-maroon: #4a0f0a;
    --card-white: #ffffff;
    --text-grey: #555555;
    --backdrop: #e9e7e4;
  }
  * { box-sizing: border-box; margin: 0; padding: 0; }
  html, body { width: 1200px; height: 912px; overflow: hidden; }
  body {
    background: var(--backdrop);
    position: relative;
    font-family: "Poppins", sans-serif;
  }
  .card {
    position: absolute;
    width: 620px;
    height: 354px;
    border-radius: 18px;
    overflow: hidden;
    box-shadow: 0 10px 30px rgba(0,0,0,0.18);
  }

  /* Services side */
  .card--services {
    left: 110px; top: 56px;
    background: var(--brand-red);
  }
  .services {
    position: absolute;
    left: 0; right: 0; top: 92px;
    display: flex;
    justify-content: center;
    gap: 48px;
  }
  .service {
    display: flex; flex-direction: column; align-items: center;
    width: 140px;
  }
  .service__icon {
    width: 120px; height: 110px;
    border-radius: 6px;
    background: var(--brand-red-light);
  }
  .service__label {
    margin-top: 14px;
    color: var(--card-white);
    font-size: 20px;
    font-weight: 500;
    letter-spacing: 0.5px;
  }

  /* Contact side */
  .card--contact {
    left: 470px; top: 500px;
    background: var(--card-white);
  }
  .brand {
    position: absolute; left: 40px; top: 48px;
    display: flex; align-items: center; gap: 12px;
  }
  .brand__dot {
    width: 30px; height: 30px; border-radius: 50%;
    background: var(--brand-red);
  }
  .brand__name {
    font-size: 30px; font-weight: 500;
    color: var(--deep-maroon);
    letter-spacing: 1px;
  }
  .person {
    position: absolute; right: 48px; top: 48px;
    text-align: right;
  }
  .person__name {
    font-family: "Roboto Condensed", sans-serif;
    font-weight: 500;
    font-size: 24px;
    color: var(--brand-red);
    letter-spacing: 0.5px;
  }
  .person__role {
    font-size: 14px; color: var(--text-grey);
  }
  .person__rule {
    position: absolute; right: 40px; top: 114px;
    width: 260px; height: 2px; background: var(--brand-red);
  }
  .accent-tab {
    position: absolute; right: 0; top: 44px;
    width: 10px; height: 34px; background: var(--brand-red);
  }
  .divider {
    position: absolute; left: 40px; top: 210px;
    width: 330px; height: 1.5px; background: var(--brand-red);
  }
  .contact {
    position: absolute; left: 40px; top: 232px;
    list-style: none;
    font-size: 17px; color: var(--text-grey);
  }
  .contact__item { display: flex; align-items: center; gap: 8px; line-height: 32px; }
  .contact__icon { width: 14px; height: 14px; flex: none; }
  .swoosh { position: absolute; right: 0; bottom: 0; }
</style>
</head>
<body>

<section class="card card--services" aria-label="Services side">
  <div class="services">
    <div class="service">
      <div class="service__icon" role="img" aria-label="Line icon of a molding press"></div>
      <span class="service__label">Molding</span>
    </div>
    <div class="service">
      <div class="service__icon" role="img" aria-label="Line icon of a 3D printer"></div>
      <span class="service__label">3D printer</span>
    </div>
    <div class="service">
      <div class="service__icon" role="img" aria-label="Line icon for casting"></div>
      <span class="service__label">Casting</span>
    </div>
  </div>
</section>

<section class="card card--contact" aria-label="Contact side">
  <div class="brand">
    <span class="brand__dot"></span>
    <span class="brand__name">Kelvar Design</span>
  </div>

  <div class="accent-tab"></div>
  <div class="person">
    <p class="person__name">DANIEL ROURKE</p>
    <p class="person__role">President</p>
  </div>
  <div class="person__rule"></div>

  <div class="divider"></div>

  <ul class="contact">
    <li class="contact__item">
      <svg class="contact__icon" viewBox="0 0 24 24" aria-hidden="true">
        <path fill="#dc2000" d="M6.6 10.8a15 15 0 0 0 6.6 6.6l2.2-2.2a1 1 0 0 1 1-.25 11.4 11.4 0 0 0 3.6.6 1 1 0 0 1 1 1V20a1 1 0 0 1-1 1A17 17 0 0 1 3 4a1 1 0 0 1 1-1h3.5a1 1 0 0 1 1 1c0 1.25.2 2.45.6 3.6a1 1 0 0 1-.25 1z"/>
      </svg>
      <span>613-582-9047</span>
    </li>
    <li class="contact__item">
      <svg class="contact__icon" viewBox="0 0 24 24" aria-hidden="true">
        <rect x="2" y="5" width="20" height="14" rx="2" fill="none" stroke="#dc2000" stroke-width="2.5"/>
        <path d="M3 6l9 7 9-7" fill="none" stroke="#dc2000" stroke-width="2.5"/>
      </svg>
      <span>mark@kelvardesign.ca</span>
    </li>
  </ul>

  <svg class="swoosh" width="300" height="200" viewBox="0 0 300 200" aria-hidden="true">
    <path d="M300 55 L300 200 L40 200 C110 150 200 90 300 55 Z" fill="var(--brand-red)"/>
    <path d="M30 200 C110 140 200 85 290 50" fill="none" stroke="var(--deep-maroon)" stroke-width="6"/>
  </svg>
</section>

</body>
</html>
```